New Business Card for Web Design/Internet Marketing Company

Looking for a great looking new business card. We are a 10 year old web design, internet marketing and website management company that works mostly with small businesses.

Our new card needs to better match the colors and style of our website, be bold, extremely usable and slightly edgy.

Target Market(s)

Small/Medium businesses that have websites

Industry/Entity Type

Internet

Requirements
Must have
• Front and back design, full color, rounded corners please

Must use the colors/style of our website (JPG provided)

INFO FOR CARDS (as readable as possible please)
Mark Lenner
President/CEO
mark@trelvanmedia.example
Phone: 520-381-7459
Toll Free: 866-381-7459
Address: 4315 W. Calloway Ave. Ste. 140, Tucson, AZ 85792

THINGS I WANT TO PROMOTE (if there is room):
1. Our Website - www.trelvanmedia.example

2. Social Media
Twitter: @trelvanmedia
Facebook: www.facebook.com/trelvanmedia

3. Our Services
Web Design
Internet Marketing
Website Management

```html
<!DOCTYPE html>
<html lang="en">
<head>
<meta charset="utf-8">
<title>Trelvan Media – Business Card</title>
<link rel="stylesheet" href="https://fonts.googleapis.com/css2?family=Source+Sans+3:wght@400;600;700&display=swap">
<style>
  :root {
    --brand-blue: #1a8fcd;
    --brand-blue-dark: #1478b0;
    --brand-orange: #f08a24;
    --ink: #4a4a4a;
    --band-grey: #5f6062;
    --paper: #ffffff;
    --backdrop: #e9e7e4;
  }
  * { box-sizing: border-box; margin: 0; padding: 0; }
  html, body { width: 1200px; height: 402px; overflow: hidden; }
  body {
    background: var(--backdrop);
    font-family: "Source Sans 3", Arial, sans-serif;
    position: relative;
  }
  .card {
    position: absolute;
    width: 524px;
    height: 292px;
    border-radius: 8px;
    overflow: hidden;
    box-shadow: 0 2px 8px rgba(0,0,0,.18);
  }
  /* Front */
  .card-front { left: 61px; top: 58px; background: var(--paper); }
  .wordmark {
    position: absolute; top: 62px; left: 0; width: 100%;
    display: flex; justify-content: center; align-items: center; gap: 10px;
  }
  .wordmark-dot {
    width: 18px; height: 18px; border-radius: 50%; background: var(--brand-orange);
  }
  .wordmark-name {
    font-weight: 700; font-size: 44px; line-height: 1; color: var(--brand-blue);
    letter-spacing: -0.5px;
  }
  .person {
    position: absolute; top: 148px; left: 0; width: 100%; text-align: center;
    color: var(--brand-blue);
  }
  .person-name { font-weight: 700; font-size: 17px; }
  .person-title { font-size: 13px; }
  .contacts {
    position: absolute; top: 186px; left: 0; width: 100%;
    display: flex; justify-content: center; gap: 12px;
    font-size: 12.5px; color: var(--ink); line-height: 20px;
  }
  .contacts-divider { width: 1px; background: #9a9a9a; margin: 2px 0; }
  .contact-line { display: flex; align-items: center; gap: 5px; }
  .contact-line svg { width: 9px; height: 9px; flex: none; }
  .front-band { position: absolute; left: 0; bottom: 0; width: 100%; height: 56px; }
  .address {
    position: absolute; left: 0; bottom: 10px; width: 100%; text-align: center;
    color: #fff; font-size: 12.5px; letter-spacing: .2px;
  }
  /* Back */
  .card-back { left: 626px; top: 58px; background: var(--brand-blue); color: #fff; text-align: center; }
  .back-wordmark {
    position: absolute; top: 76px; left: 0; width: 100%;
    display: flex; justify-content: center; align-items: center; gap: 10px;
  }
  .back-wordmark .wordmark-dot { background: #fff; width: 14px; height: 14px; }
  .back-wordmark .wordmark-name { color: #fff; font-size: 40px; }
  .services-heading {
    position: absolute; top: 158px; left: 0; width: 100%;
    font-size: 22px; font-weight: 600;
  }
  .services-rule {
    position: absolute; top: 189px; left: 50%; width: 178px; margin-left: -89px;
    height: 2px; background: #fff;
  }
  .services-list {
    position: absolute; top: 204px; left: 0; width: 100%;
    font-size: 19px; line-height: 26px;
  }
  .social {
    position: absolute; top: 268px; left: 0; width: 100%;
    display: flex; justify-content: center; gap: 36px; font-size: 13px;
  }
  .social-item { display: flex; align-items: center; gap: 5px; }
  .social-square { width: 12px; height: 12px; border-radius: 2px; background: rgba(255,255,255,.85); }
</style>
</head>
<body>

<section class="card card-front" aria-label="Card front">
  <div class="wordmark">
    <span class="wordmark-dot"></span>
    <span class="wordmark-name">Trelvan Media</span>
  </div>

  <p class="person"><span class="person-name">Mark Lenner,</span> <span class="person-title">President/CEO</span></p>

  <div class="contacts">
    <div class="contacts-col">
      <div class="contact-line">
        <svg viewBox="0 0 10 10"><circle cx="5" cy="5" r="4.5" fill="none" stroke="#1a8fcd" stroke-width="1.2"/><path d="M3 3.2 4.2 3l.6 1.4-.7.6a3.5 3.5 0 0 0 1.4 1.4l.6-.7 1.4.6-.2 1.2C5 7.5 2.6 5.2 3 3.2z" fill="#1a8fcd"/></svg>
        <span>520-381-7459</span>
      </div>
      <div class="contact-line">
        <svg viewBox="0 0 10 10"><circle cx="5" cy="5" r="4.5" fill="none" stroke="#1a8fcd" stroke-width="1.2"/><path d="M3 3.2 4.2 3l.6 1.4-.7.6a3.5 3.5 0 0 0 1.4 1.4l.6-.7 1.4.6-.2 1.2C5 7.5 2.6 5.2 3 3.2z" fill="#1a8fcd"/></svg>
        <span>866-381-7459</span>
      </div>
    </div>
    <div class="contacts-divider"></div>
    <div class="contacts-col">
      <div class="contact-line">
        <svg viewBox="0 0 10 10"><rect x="0.5" y="2" width="9" height="6" fill="#1a8fcd"/><path d="M.5 2 5 5.5 9.5 2" fill="none" stroke="#fff" stroke-width=".8"/></svg>
        <span>mark@trelvanmedia.example</span>
      </div>
      <div class="contact-line">
        <svg viewBox="0 0 10 10"><circle cx="5" cy="5" r="4.3" fill="none" stroke="#1a8fcd" stroke-width="1"/><ellipse cx="5" cy="5" rx="1.8" ry="4.3" fill="none" stroke="#1a8fcd" stroke-width=".8"/><path d="M.7 5h8.6" stroke="#1a8fcd" stroke-width=".8"/></svg>
        <span>www.trelvanmedia.example</span>
      </div>
    </div>
  </div>

  <svg class="front-band" viewBox="0 0 524 56" preserveAspectRatio="none" aria-hidden="true">
    <path d="M0 16 Q262 -6 524 6 L524 56 L0 56 Z" fill="var(--band-grey)"/>
    <path d="M0 14 Q262 -10 500 2" fill="none" stroke="var(--brand-blue)" stroke-width="4"/>
  </svg>
  <p class="address">4315 W. Calloway Ave. Ste. 140, Tucson, AZ 85792</p>
</section>

<section class="card card-back" aria-label="Card back">
  <div class="back-wordmark">
    <span class="wordmark-dot"></span>
    <span class="wordmark-name">Trelvan Media</span>
  </div>
  <h2 class="services-heading">Our Services</h2>
  <div class="services-rule"></div>
  <p class="services-list">Web Design &nbsp;•&nbsp; Internet Marketing<br>Website Management</p>
  <div class="social">
    <span class="social-item"><span class="social-square"></span>@trelvanmedia</span>
    <span class="social-item"><span class="social-square"></span>trelvanmedia</span>
  </div>
</section>

</body>
</html>
```